Amazing Sexy Elegant Eyecatching Wine Label

We need a label designed for our wine which is going to be produced very soon.

Needs to be on a grey scale, as colours increase the price per label dramatically.

Needs to have the "Crown" logo (file attached) included on the front and back label. Logo can be in black/white but can not be changed in any way, circle around the crown must stay there as well.

We are still unsure of whether to use "Harrowdale Wine" or "Harrowdale" as the brand for the label, if you could submit designs based around the two names we would appreciate that.

We will have 5 varieties, including; Sauvignon Blanc, Chardonnay, Pinot Gris, Riesling and Pinot Noir. So text needs to be easily changed.

We are after an image on the label which is modern and eye catching, even in a grey scale.

Please see other attached files for an idea we have done previously, we want something a bit more "designer" though. Some information on the label is a legal requirement and needs to be kept.

Target Market(s)

Wine Consumers

Requirements
Must have
• Crown Logo, Harrowdale/Harrowdale Wine brand, Grey Scale, Modern Design

```html
<!DOCTYPE html>
<html lang="en">
<head>
<meta charset="utf-8">
<title>Harrowdale Wine – Back Label</title>
<link rel="stylesheet" href="https://fonts.googleapis.com/css2?family=Josefin+Sans:wght@300;400;600&family=Lora:wght@400&display=swap">
<style>
  :root {
    --page: #d6d6d6;
    --label: #f1f1f1;
    --ink: #2b2b2b;
    --ink-soft: #555555;
    --rule: #8a8a8a;
    --mark: #3a3a3a;
  }
  * { box-sizing: border-box; margin: 0; padding: 0; }
  html, body { width: 1200px; height: 2488px; overflow: hidden; background: var(--page); }
  .canvas { position: relative; width: 1200px; height: 2488px; }

  .label {
    position: absolute; left: 50px; top: 324px; width: 1100px; height: 1840px;
    background: var(--label); color: var(--ink); text-align: center;
    font-family: "Lora", serif;
  }
  .label__frame {
    position: absolute; inset: 30px; border: 3px solid var(--rule);
  }
  .label__frame::after {
    content: ""; position: absolute; inset: 10px; border: 1.5px solid var(--rule);
  }

  .brand-mark {
    position: absolute; left: 50%; top: 250px; transform: translateX(-50%);
    display: flex; flex-direction: column; align-items: center; gap: 18px;
  }
  .brand-mark__circle {
    width: 150px; height: 150px; border: 5px solid var(--ink); border-radius: 50%;
  }
  .brand-mark__name {
    font-family: "Josefin Sans", sans-serif; font-weight: 400; font-size: 30px;
    letter-spacing: 6px; text-transform: uppercase; color: var(--ink);
  }

  .title {
    position: absolute; left: 0; right: 0; top: 555px;
    font-family: "Josefin Sans", sans-serif; font-weight: 300; font-size: 76px;
    letter-spacing: 3px; color: var(--ink);
  }

  .tasting {
    position: absolute; left: 150px; right: 150px; top: 670px;
    font-size: 27px; line-height: 1.55; color: var(--ink-soft);
  }
  .tasting p + p { margin-top: 34px; }

  .flourish {
    position: absolute; left: 50%; width: 130px; height: 26px; margin-left: -65px;
    background: linear-gradient(90deg, transparent, var(--mark) 30%, var(--mark) 70%, transparent);
    border-radius: 13px; opacity: .75;
  }
  .flourish--top { top: 975px; }
  .flourish--bottom { top: 1105px; }

  .web {
    position: absolute; left: 0; right: 0; top: 1030px;
    font-size: 34px; letter-spacing: 1px; color: var(--ink);
  }

  .credits {
    position: absolute; left: 0; right: 0; top: 1185px;
    font-family: "Josefin Sans", sans-serif; text-transform: uppercase; color: var(--ink);
  }
  .credits__role { font-size: 19px; font-weight: 600; letter-spacing: 2px; }
  .credits__party { font-family: "Lora", serif; font-size: 25px; letter-spacing: 1px; margin: 8px 0 22px; }

  .footer {
    position: absolute; left: 70px; right: 70px; top: 1440px; height: 300px;
  }
  .pictogram { position: absolute; background: var(--mark); }
  .pictogram--bottle { left: 20px; top: 40px; width: 70px; height: 240px; border-radius: 18px 18px 6px 6px; }
  .volume {
    position: absolute; left: 28px; top: 150px; width: 54px;
    font-family: "Josefin Sans", sans-serif; font-size: 15px; font-weight: 600;
    color: var(--label); line-height: 1.2;
  }
  .pictogram--glass { left: 110px; top: 130px; width: 36px; height: 90px; border-radius: 4px 4px 18px 18px; }
  .pictogram--pregnancy {
    left: 250px; top: 180px; width: 100px; height: 100px; border-radius: 50%;
    background: linear-gradient(160deg, #4a4a4a, #222);
  }
  .responsibly {
    position: absolute; left: 230px; top: 100px; width: 330px;
    font-family: "Josefin Sans", sans-serif; font-weight: 600; font-size: 28px;
    letter-spacing: 1.5px; text-transform: uppercase; text-align: left;
  }
  .partner-badge {
    position: absolute; left: 410px; top: 195px; width: 150px; height: 70px;
    background: var(--mark); border-radius: 8px;
  }
  .pictogram--bottles { right: 170px; top: 40px; width: 130px; height: 240px; border-radius: 20px 20px 6px 6px; background: linear-gradient(90deg, var(--mark) 45%, transparent 45%, transparent 55%, var(--mark) 55%); }
</style>
</head>
<body>
<main class="canvas">
  <section class="label">
    <div class="label__frame"></div>

    <div class="brand-mark">
      <div class="brand-mark__circle"></div>
      <div class="brand-mark__name">Harrowdale</div>
    </div>

    <h1 class="title">Harrowdale Wine</h1>

    <div class="tasting">
      <p>Crisp, light amber color with good acids. The taste is reminiscent of freshly cut herbs with a hint of mint.</p>
      <p>It will enhance rather than overpower any dish. A wonderful complement to any light dish and delightfully refreshing. Serve lightly chilled.</p>
    </div>

    <div class="flourish flourish--top" role="img" aria-label="Decorative scroll ornament"></div>
    <p class="web">www.harrowdaleimports.co.nz</p>
    <div class="flourish flourish--bottom" role="img" aria-label="Decorative scroll ornament"></div>

    <div class="credits">
      <p class="credits__role">Produced and bottled by</p>
      <p class="credits__party">Kestrel Hill Wines | Marlborough, NZ</p>
      <p class="credits__role">Distributed by</p>
      <p class="credits__party">Harrowdale Imports Ltd</p>
    </div>

    <div class="footer">
      <div class="pictogram pictogram--bottle" role="img" aria-label="Bottle pictogram"></div>
      <div class="volume">13%<br>750 ML</div>
      <div class="pictogram pictogram--glass" role="img" aria-label="Wine glass pictogram"></div>
      <p class="responsibly">Drink responsibly</p>
      <div class="pictogram pictogram--pregnancy" role="img" aria-label="Pregnancy warning symbol"></div>
      <div class="partner-badge" role="img" aria-label="Responsible drinking partner badge"></div>
      <div class="pictogram pictogram--bottles" role="img" aria-label="Standard drinks pictogram"></div>
    </div>
  </section>
</main>
</body>
</html>
```